Beef cattle farm needs signs which can be seen from roadside

We would like submissions of artwork for a sign that will hang from a fence or gate and will be seen by passing cars.

Existing logo and branding theme for the company is attached.

Signage can be between 900mm x 400mm - 1200mm x 600mm

Industry/Entity Type

Farm

Requirements
Must have
• the Signs should have the following information:
• Company name: Wendlow Grazing Company
• Address: 417 Corrigan Flat Road
• Contact number: 0431 862 407
• email address: admin@wendlowgrazingcompany.com.au
• - Logo and branding as per attached artwork

```html
<!DOCTYPE html>
<html lang="en">
<head>
<meta charset="utf-8">
<title>Wendlow Grazing Company – Roadside Sign</title>
<link href="https://fonts.googleapis.com/css2?family=Montserrat:wght@500&family=Arimo:wght@400;700&display=swap" rel="stylesheet">
<style>
  :root {
    --backdrop: #878685;
    --sign-white: #ffffff;
    --brand-green: #155f36;
    --panel-green-dark: #05371d;
    --panel-green: #0b4f2c;
    --edge-grey: #c9cacc;
    --text-light: #ffffff;
  }
  * { margin: 0; padding: 0; box-sizing: border-box; }
  html, body {
    width: 1200px;
    height: 655px;
    overflow: hidden;
    background: var(--backdrop);
  }
  .sign {
    position: absolute;
    left: 109px;
    top: 108px;
    width: 981px;
    height: 437px;
    background: var(--sign-white);
    overflow: hidden;
  }
  .sign__swoosh {
    position: absolute;
    inset: 0;
    width: 981px;
    height: 437px;
  }
  .brand {
    position: absolute;
    left: 50px;
    top: 37px;
    width: 340px;
    text-align: center;
  }
  .brand__mark {
    display: block;
    width: 230px;
    height: 230px;
    margin: 0 auto;
    border-radius: 50%;
    background: var(--brand-green);
  }
  .brand__name {
    font-family: "Montserrat", sans-serif;
    font-weight: 500;
    color: var(--brand-green);
    line-height: 1;
  }
  .brand__name-main {
    display: block;
    margin-top: 22px;
    font-size: 62px;
    letter-spacing: 1px;
  }
  .brand__name-sub {
    display: block;
    margin-top: 8px;
    font-size: 24px;
    letter-spacing: 0.5px;
  }
  .contact {
    position: absolute;
    right: 30px;
    top: 264px;
    text-align: right;
    color: var(--text-light);
    font-family: "Arimo", sans-serif;
  }
  .contact__address {
    font-size: 22px;
    font-weight: 400;
    line-height: 1;
  }
  .contact__email {
    margin-top: 12px;
    font-size: 20px;
    font-weight: 700;
    line-height: 1;
  }
  .contact__phone {
    margin-top: 34px;
    font-size: 38px;
    font-weight: 700;
    line-height: 1;
  }
</style>
</head>
<body>
  <main class="sign">
    <svg class="sign__swoosh" viewBox="0 0 981 437" aria-hidden="true">
      <defs>
        <linearGradient id="panelFill" x1="0" y1="0" x2="1" y2="0">
          <stop offset="0" stop-color="var(--panel-green-dark)"/>
          <stop offset="1" stop-color="var(--panel-green)"/>
        </linearGradient>
        <linearGradient id="edgeFill" x1="0" y1="0" x2="1" y2="0">
          <stop offset="0" stop-color="#ffffff"/>
          <stop offset="0.6" stop-color="var(--edge-grey)"/>
        </linearGradient>
      </defs>
      <path d="M 840 0 C 600 40, 410 230, 455 437 L 981 437 L 981 0 Z" fill="url(#edgeFill)"/>
      <path d="M 880 0 C 620 50, 400 250, 462 437 L 981 437 L 981 0 Z" fill="url(#panelFill)"/>
    </svg>

    <div class="brand">
      <span class="brand__mark" aria-hidden="true"></span>
      <p class="brand__name">
        <span class="brand__name-main">WENDLOW</span>
        <span class="brand__name-sub">GRAZING COMPANY</span>
      </p>
    </div>

    <address class="contact" style="font-style: normal;">
      <p class="contact__address">417 Corrigan Flat Road</p>
      <p class="contact__email">admin@wendlowgrazingcompany.com.au</p>
      <p class="contact__phone">Call : 0431 862 407</p>
    </address>
  </main>
</body>
</html>
```